Business Card Design

Business sales of reconditioned / used batteries with mobile delivery and install services. Customers base majority are auto car sales lots and individuals.

Card need to convey quality product reliability and quick prompt professional service.

Card must reflect excellence in customer care and product being offered

Target Market(s)

Auto car lots new and used. Auto repair shops. Individuals.

Industry/Entity Type

Business

Contact Information for Business Card

Batteries Q-Swift
Cars, Trucks, Boats, Motorcycles, lawn mowers, power tools
Delivery & install available most vehicles
Mon-Sat 9-6pm
Dale Morrick 501-738-2054
*product warranty 6 month shelf life battery/1 year blems battery

```html
<!DOCTYPE html>
<html lang="en">
<head>
<meta charset="UTF-8">
<title>Northgate Cell Supply – Business Card</title>
<link href="https://fonts.googleapis.com/css2?family=Lato:wght@400;700;900&display=swap" rel="stylesheet">
<style>
  :root {
    --backdrop: #5e5e5e;
    --card-black: #000000;
    --brand-blue: #1f7cc4;
    --accent-orange: #f47a20;
    --phone-teal: #1aa3c4;
    --name-blue: #2c5fa8;
    --white: #ffffff;
  }
  * { margin: 0; padding: 0; box-sizing: border-box; }
  html, body {
    width: 1200px;
    height: 900px;
    overflow: hidden;
    background: var(--backdrop);
    font-family: "Lato", Arial, sans-serif;
  }
  .canvas {
    width: 1200px;
    height: 900px;
    display: flex;
    align-items: center;
    justify-content: center;
  }
  .business-card {
    position: relative;
    width: 1050px;
    height: 600px;
    background: var(--card-black);
    overflow: hidden;
    box-shadow: 0 20px 40px rgba(0, 0, 0, 0.35);
  }
  .warranty-wave {
    position: absolute;
    inset: 0;
    width: 100%;
    height: 100%;
  }
  .card-text {
    position: absolute;
    left: 0;
    width: 100%;
    text-align: center;
  }
  .brand-name {
    top: 95px;
    font-size: 54px;
    font-weight: 700;
    color: var(--brand-blue);
    letter-spacing: -0.5px;
  }
  .service-line {
    font-size: 27px;
    color: var(--accent-orange);
    display: inline-block;
    padding: 0 4px 4px;
    border-bottom: 2px solid var(--accent-orange);
  }
  .services { top: 182px; }
  .services-second { top: 226px; }
  .service-line strong { font-weight: 700; }
  .contact-name {
    top: 292px;
    font-size: 38px;
    color: var(--name-blue);
    letter-spacing: 1px;
  }
  .contact-name .first { font-weight: 400; margin-right: 10px; }
  .contact-name .last { font-weight: 700; }
  .contact-phone {
    top: 346px;
    font-size: 25px;
    color: var(--phone-teal);
    letter-spacing: 0.5px;
  }
  .contact-phone .label { font-weight: 900; }
  .warranty-title {
    top: 452px;
    font-size: 31px;
    font-weight: 700;
    color: var(--white);
    letter-spacing: 0.5px;
  }
  .warranty-terms {
    top: 505px;
    font-size: 22px;
    font-weight: 700;
    color: var(--white);
    letter-spacing: 1px;
  }
</style>
</head>
<body>
<main class="canvas">
  <section class="business-card" aria-label="Northgate Cell Supply business card">
    <svg class="warranty-wave" viewBox="0 0 1050 600" preserveAspectRatio="none" aria-hidden="true">
      <path d="M0,462 C300,372 650,372 1050,412 L1050,600 L0,600 Z" fill="var(--white)"/>
      <path d="M0,470 C300,380 650,380 1050,420 L1050,600 L0,600 Z" fill="var(--accent-orange)"/>
    </svg>

    <h1 class="card-text brand-name">Northgate Cell Supply</h1>

    <p class="card-text services"><span class="service-line">Trucks, Boats, Motorcycles, lawn mowers, power tools Delivery</span></p>
    <p class="card-text services-second"><span class="service-line">&amp; install available most vehicles <strong>Mon-Sat 9-6pm</strong></span></p>

    <p class="card-text contact-name"><span class="first">DALE</span><span class="last">MORRICK</span></p>
    <p class="card-text contact-phone"><span class="label">PHONE:</span> 501-738-2054</p>

    <h2 class="card-text warranty-title">PRODUCT WARRANTY</h2>
    <p class="card-text warranty-terms">6 MONTH SHELF LIFE BATTERY/1 YEAR BLEMS BATTERY</p>
  </section>
</main>
</body>
</html>
```